We are a local Communty Pharmacy wishing to promote and market a specialised Pharmaceutical Service

We would like a design that is professional and enticing ( according to the brief In attached files)
We wish to Market Compounding Pharmacy as a specialist side of our business.
We have the expertise a purpose built preparation laboratory.
The main purpose is an Internet presence that entices prospective patients to contact or visit our physical store.

Target Market(s)

Patients Medicos and Veterinary clients

Industry/Entity Type

Pharmacy

Coding

Coded - Design and coding required

Number of Pages Required

1 page

Requirements
Must have
• Clear friendly image
Nice to have
• soft enticing feel
Should not have
• No crass loud unprofessional elements

```html
<!DOCTYPE html>
<html lang="en">
<head>
<meta charset="utf-8">
<title>Brightwell Pharmacy – Compounding</title>
<link href="https://fonts.googleapis.com/css2?family=Open+Sans:wght@300;400;600;700&display=swap" rel="stylesheet">
<style>
:root{
  --lime:#c3d62f;
  --lime-dark:#a9bc1e;
  --teal:#6fc4c1;
  --teal-dark:#58b0ad;
  --ink:#4d5358;
  --muted:#7c8287;
  --white:#ffffff;
  --page:#ffffff;
}
*{box-sizing:border-box;margin:0;padding:0}
html,body{width:668px;height:1200px;overflow:hidden}
body{background:var(--page);font-family:"Open Sans",sans-serif;color:var(--ink);position:relative}
.topbar{position:absolute;top:0;left:0;width:668px;height:26px;background:var(--lime);display:flex;justify-content:flex-end;align-items:center;gap:22px;padding-right:46px;font-size:9px;color:var(--white)}
.topbar span{display:flex;align-items:center;gap:6px}
.header{position:absolute;top:26px;left:0;width:668px;height:54px;display:flex;align-items:center;justify-content:space-between;padding:0 46px}
.brand{display:flex;align-items:center;gap:8px;font-weight:600;font-size:15px;color:var(--teal-dark)}
.brand-dot{width:26px;height:26px;border-radius:50%;background:var(--teal)}
.nav{display:flex;gap:26px;font-size:8.5px;font-weight:600;color:var(--ink);letter-spacing:.3px}
.hero{position:absolute;top:80px;left:0;width:668px;height:342px;background:linear-gradient(100deg,#cfe3ea 0%,#eef4f5 45%,#f6f2ee 60%,#d7e6ea 100%)}
.hero-copy{position:absolute;left:46px;top:152px}
.hero-title{font-size:27px;font-weight:600;color:var(--white);text-shadow:0 1px 4px rgba(60,90,100,.35)}
.hero-line{display:inline-block;margin-top:4px;padding:2px 8px;background:rgba(70,110,120,.55);color:var(--lime);font-size:14px;font-weight:600}
.hero-line.small{font-size:11px;font-weight:400}
.features{position:absolute;top:450px;left:45px;width:578px;display:flex;gap:4px}
.feature{flex:1;height:150px;background:var(--teal);color:var(--white);text-align:center;padding-top:26px}
.feature.alt{background:var(--lime)}
.feature h3{font-size:12px;font-weight:400;margin-top:18px;letter-spacing:.3px}
.feature p{font-size:8px;line-height:12px;margin:6px auto 0;width:140px;opacity:.9}
.about{position:absolute;top:620px;left:45px;width:578px}
.about h2{font-size:15px;font-weight:600;color:var(--ink)}
.about h2 em{font-style:normal;color:var(--lime-dark)}
.about p{font-size:9.5px;line-height:16px;color:var(--muted);margin-top:12px}
.btn{display:inline-block;margin-top:18px;background:var(--lime);color:var(--white);font-size:8px;font-weight:600;padding:6px 12px}
.contact{position:absolute;top:935px;left:45px;width:578px;height:185px;background:var(--lime);display:flex;padding:14px}
.contact-info{width:270px;color:var(--white);padding-top:4px}
.contact-info h2{font-size:14px;font-weight:400}
.contact-info h2 b{font-weight:600;color:#f4fbd0}
.contact-info p{font-size:8.5px;line-height:13px;margin-top:8px}
.contact-row{display:flex;align-items:center;gap:8px;font-size:8.5px;margin-top:10px}
.contact-row svg{flex:none}
.map{flex:1;background:linear-gradient(135deg,#e8ebe4,#dfe4dc)}
.footer{position:absolute;top:1140px;left:0;width:668px;height:60px;background:var(--teal);color:var(--white);padding:10px 46px 0}
.footer-nav{display:flex;align-items:center;gap:30px;font-size:8px;font-weight:600}
.footer-social{margin-left:auto;display:flex;align-items:center;gap:5px;font-weight:400}
.footer-social i{width:12px;height:12px;border-radius:50%;background:var(--white);display:block}
.copyright{font-size:7.5px;margin-top:12px;opacity:.9}
</style>
</head>
<body>
<div class="topbar">
  <span><svg width="9" height="9" viewBox="0 0 24 24"><path fill="#fff" d="M6.6 10.8a15.1 15.1 0 0 0 6.6 6.6l2.2-2.2c.3-.3.7-.4 1-.2 1.1.4 2.3.6 3.6.6.6 0 1 .4 1 1V20c0 .6-.4 1-1 1C10.6 21 3 13.4 3 4c0-.6.4-1 1-1h3.5c.6 0 1 .4 1 1 0 1.3.2 2.5.6 3.6.1.3 0 .7-.2 1z"/></svg>(65) 6100 2040</span>
  <span><svg width="10" height="8" viewBox="0 0 20 14"><rect x="1" y="1" width="18" height="12" fill="none" stroke="#fff" stroke-width="1.6"/><path d="M1 1l9 7 9-7" fill="none" stroke="#fff" stroke-width="1.6"/></svg>hello@brightwellrx.com</span>
</div>

<header class="header">
  <div class="brand"><span class="brand-dot"></span>Brightwell Pharmacy</div>
  <nav class="nav"><span>HOME</span><span>ABOUT US</span><span>LOCATIONS</span><span>TIMINGS</span><span>CONTACT</span></nav>
</header>

<section class="hero" role="img" aria-label="Smiling pharmacist in a white coat standing between bright pharmacy shelves">
  <div class="hero-copy">
    <h1 class="hero-title">Compounding Pharmacy</h1>
    <div><span class="hero-line">Medicine made to measure for you</span></div>
    <div><span class="hero-line small">Prepared in our own purpose built laboratory</span></div>
  </div>
</section>

<section class="features">
  <div class="feature">
    <svg width="34" height="38" viewBox="0 0 34 38"><path d="M17 2l14 8v18l-14 8-14-8V10z" fill="none" stroke="#fff" stroke-width="2"/><path d="M17 10l7 4v9l-7 4-7-4v-9z" fill="#fff"/></svg>
    <h3>WE DO COMPOUNDING</h3>
    <p>Tailored strengths, flavours and forms made for each patient.</p>
  </div>
  <div class="feature alt">
    <svg width="38" height="38" viewBox="0 0 38 38"><path d="M4 16h30c0 9-7 15-15 15S4 25 4 16z" fill="none" stroke="#fff" stroke-width="2"/><path d="M24 4l-6 12" stroke="#fff" stroke-width="3" stroke-linecap="round"/><path d="M13 34h12" stroke="#fff" stroke-width="2"/></svg>
    <h3>WHERE WE ARE</h3>
    <p>Visit our store and laboratory in the heart of town.</p>
  </div>
  <div class="feature">
    <svg width="38" height="38" viewBox="0 0 38 38"><circle cx="19" cy="19" r="15" fill="none" stroke="#fff" stroke-width="2"/><path d="M19 10v9l6 4" fill="none" stroke="#fff" stroke-width="2" stroke-linecap="round"/></svg>
    <h3>WHEN WE ARE THERE</h3>
    <p>Open six days a week, with a pharmacist always on hand.</p>
  </div>
</section>

<section class="about">
  <h2>WHAT IS <em>COMPOUNDING PHARMACY?</em></h2>
  <p>Until the early twentieth century, nearly every medicine was prepared by hand in the pharmacy for each patient. Mass manufacturing later made standard doses common, and the craft became rare.</p>
  <p>Today compounding meets needs that factory medicines cannot: a dose strength that is not sold, a form that is easier to take, or a formula without an ingredient you react to.</p>
  <p>We prepare creams, capsules, liquids and lozenges in our purpose built laboratory, working closely with your doctor or vet to get every detail right for the person or animal in your care.</p>
  <p>Every preparation is checked by a qualified pharmacist before it leaves our bench, and our team is always happy to talk through how and when to use it.</p>
  <span class="btn">› READ MORE</span>
</section>

<section class="contact">
  <div class="contact-info">
    <h2>HOW YOU CAN <b>VISIT CONTACT</b></h2>
    <p>Call, email or drop in to talk with a pharmacist about a preparation for you, your family or your pet.</p>
    <div class="contact-row"><svg width="12" height="14" viewBox="0 0 12 16"><path d="M6 0a6 6 0 0 0-6 6c0 4.5 6 10 6 10s6-5.5 6-10a6 6 0 0 0-6-6z" fill="#fff"/><circle cx="6" cy="6" r="2.2" fill="#c3d62f"/></svg>12 Elmstead Road, Singapore 000000</div>
    <div class="contact-row"><svg width="13" height="10" viewBox="0 0 20 14"><rect x="1" y="1" width="18" height="12" fill="#fff"/><path d="M1 1l9 7 9-7" fill="none" stroke="#c3d62f" stroke-width="1.6"/></svg>hello@brightwellrx.com</div>
    <div class="contact-row"><svg width="12" height="12" viewBox="0 0 24 24"><path fill="#fff" d="M6.6 10.8a15.1 15.1 0 0 0 6.6 6.6l2.2-2.2c.3-.3.7-.4 1-.2 1.1.4 2.3.6 3.6.6.6 0 1 .4 1 1V20c0 .6-.4 1-1 1C10.6 21 3 13.4 3 4c0-.6.4-1 1-1h3.5c.6 0 1 .4 1 1 0 1.3.2 2.5.6 3.6.1.3 0 .7-.2 1z"/></svg>(65) 6100 2040</div>
  </div>
  <div class="map" role="img" aria-label="Street map showing the pharmacy location"></div>
</section>

<footer class="footer">
  <div class="footer-nav">
    <span>HOME</span><span>ABOUT US</span><span>LOCATIONS</span><span>TIMINGS</span><span>CONTACT</span>
    <span class="footer-social">Connect With Us <i></i><i></i><i></i><i></i></span>
  </div>
  <div class="copyright">Brightwell Pharmacy © 2015 All Rights Reserved</div>
</footer>
</body>
</html>
```